Market Research firm needs updated business cards with new logo

We need the logo to be included somewhere on the card (attached). We would also like the phrases "Impartial, Rigorous, Thorough" and "Insight You Can Rely On" somewhere on the card. Front or back. Our colors are hex codes 6075a7, e48d25 and 5a5b5b. Though you are certainly not limited to those shades, whatever you produce should coordinate with them. I have also attached our favicon. Feel free to use it in your design, but please do not use it to replace the full logo.

Contact Information for Business Card

see project description

Font styles to use
Other font styles liked:
• Open Sans

Requirements
Must have
• the logo
• We use Open Sans font

```html
<!DOCTYPE html>
<html lang="en">
<head>
<meta charset="utf-8">
<title>Halvane Research – Business Cards</title>
<link rel="stylesheet" href="https://fonts.googleapis.com/css2?family=Open+Sans:wght@400;600;700;800&display=swap">
<style>
  :root {
    --brand-blue: #6075a7;
    --brand-orange: #e48d25;
    --brand-grey: #5a5b5b;
    --bar-dark: #4d4e50;
    --paper: #ffffff;
    --stage: #c9c9c9;
  }
  * { box-sizing: border-box; margin: 0; padding: 0; }
  html, body { width: 1200px; height: 900px; overflow: hidden; }
  body {
    background: var(--stage);
    font-family: "Open Sans", Arial, sans-serif;
    position: relative;
  }
  .card {
    position: absolute;
    left: 320px;
    width: 560px;
    height: 320px;
    border-radius: 18px;
    overflow: hidden;
    background: var(--paper);
    box-shadow: 0 6px 18px rgba(0,0,0,.18);
  }
  .card--front { top: 95px; }
  .card--back { top: 485px; }
  .card__art { position: absolute; inset: 0; }

  .wordmark {
    position: absolute;
    display: flex;
    align-items: center;
    gap: 8px;
    font-weight: 600;
    color: var(--brand-grey);
    letter-spacing: -0.3px;
    white-space: nowrap;
  }
  .wordmark__dot {
    width: 13px; height: 13px;
    border-radius: 50%;
    background: var(--brand-orange);
  }
  .card--front .wordmark { left: 62px; top: 128px; font-size: 30px; }
  .card--back .wordmark { left: 40px; top: 40px; font-size: 24px; }

  .tagline {
    position: absolute;
    left: 40px; top: 206px;
    width: 320px;
    text-align: center;
    color: var(--paper);
    font-size: 13px;
    line-height: 1.45;
  }

  .person { position: absolute; left: 68px; top: 106px; }
  .person__name {
    font-size: 24px; font-weight: 800;
    color: var(--brand-blue); letter-spacing: .3px;
  }
  .person__role {
    margin: 4px 0 0 22px;
    font-size: 14px; font-weight: 800;
    color: var(--brand-blue);
  }
  .contact {
    position: absolute; left: 70px; top: 188px;
    list-style: none;
  }
  .contact__item {
    display: flex; align-items: center; gap: 12px;
    font-size: 12.5px; color: var(--brand-blue);
    height: 21px;
    white-space: nowrap;
  }
  .contact__item svg { width: 12px; height: 12px; fill: var(--brand-blue); flex: none; }
  .contact__item--caps { font-size: 11.5px; }
</style>
</head>
<body>

<section class="card card--front" aria-label="Card front">
  <svg class="card__art" viewBox="0 0 560 320" aria-hidden="true">
    <polygon points="0,188 300,188 400,258 400,320 0,320" fill="var(--brand-blue)"/>
    <line x1="312" y1="168" x2="398" y2="226" stroke="var(--brand-blue)" stroke-width="2"/>
    <rect x="400" y="0" width="14" height="320" fill="var(--bar-dark)"/>
    <rect x="414" y="0" width="146" height="320" fill="var(--brand-blue)"/>
  </svg>
  <div class="wordmark"><span class="wordmark__dot"></span>Halvane Research</div>
  <p class="tagline">"Impartial, Rigorous, Thorough"<br>and "Insight You Can Rely On"</p>
</section>

<section class="card card--back" aria-label="Card back">
  <svg class="card__art" viewBox="0 0 560 320" aria-hidden="true">
    <line x1="360" y1="0" x2="360" y2="98" stroke="var(--brand-blue)" stroke-width="2"/>
    <line x1="405" y1="0" x2="405" y2="292" stroke="var(--brand-blue)" stroke-width="2"/>
    <line x1="0" y1="292" x2="405" y2="292" stroke="var(--brand-blue)" stroke-width="2"/>
    <rect x="420" y="0" width="14" height="320" fill="var(--bar-dark)"/>
    <rect x="434" y="0" width="126" height="320" fill="var(--brand-blue)"/>
  </svg>
  <div class="wordmark"><span class="wordmark__dot"></span>Halvane Research</div>
  <div class="person">
    <h1 class="person__name">MAREN HOLLOWAY</h1>
    <p class="person__role">LIFE COACH</p>
  </div>
  <ul class="contact">
    <li class="contact__item">
      <svg viewBox="0 0 24 24"><path d="M6.6 10.8a15 15 0 0 0 6.6 6.6l2.2-2.2a1 1 0 0 1 1-.25 11.4 11.4 0 0 0 3.6.57 1 1 0 0 1 1 1V20a1 1 0 0 1-1 1A17 17 0 0 1 3 4a1 1 0 0 1 1-1h3.5a1 1 0 0 1 1 1c0 1.25.2 2.45.57 3.6a1 1 0 0 1-.25 1z"/></svg>
      410-555-0187
    </li>
    <li class="contact__item">
      <svg viewBox="0 0 24 24"><path d="M12 2a10 10 0 1 0 0 20 10 10 0 0 0 0-20zm6.9 6h-2.9a15 15 0 0 0-1.4-3.6A8 8 0 0 1 18.9 8zM12 4c.8 1.2 1.5 2.5 1.9 4h-3.8c.4-1.5 1.1-2.8 1.9-4zM4.3 14a8 8 0 0 1 0-4h3.4a16 16 0 0 0 0 4zm.8 2h2.9c.3 1.3.8 2.5 1.4 3.6A8 8 0 0 1 5.1 16zM8 8H5.1a8 8 0 0 1 4.3-3.6C8.8 5.5 8.3 6.7 8 8zm4 12c-.8-1.2-1.5-2.5-1.9-4h3.8c-.4 1.5-1.1 2.8-1.9 4zm2.3-6H9.7a14.7 14.7 0 0 1 0-4h4.6a14.7 14.7 0 0 1 0 4zm.3 5.6c.6-1.1 1.1-2.3 1.4-3.6h2.9a8 8 0 0 1-4.3 3.6zm1.7-5.6a16 16 0 0 0 0-4h3.4a8 8 0 0 1 0 4z"/></svg>
      www.northfieldstudio.com
    </li>
    <li class="contact__item contact__item--caps">
      <svg viewBox="0 0 24 24"><path d="M2 5h20v14H2zm2 2v.5l8 5 8-5V7l-8 5z"/></svg>
      MAREN@CALMCOUNSELHQ.COM
    </li>
    <li class="contact__item">
      <svg viewBox="0 0 24 24"><path d="M12 2a7 7 0 0 0-7 7c0 5.2 7 13 7 13s7-7.8 7-13a7 7 0 0 0-7-7zm0 9.5A2.5 2.5 0 1 1 12 6.5a2.5 2.5 0 0 1 0 5z"/></svg>
      1840 Orchard Lane Easton, MD 21601
    </li>
  </ul>
</section>

</body>
</html>
```